The Copper Kite Website Redesign

I want a new design and website for www.thecopperkitebrookvale.com where part of the home page includes our daily specials from our POS Toast to be pulled from API. I have included photos and links to give you a better feel for the style of our restaurant.

Coding

Coded - Design and coding required

```html
<!DOCTYPE html>
<html lang="en">
<head>
<meta charset="utf-8">
<title>The Copper Kite — Home</title>
<link rel="stylesheet" href="https://fonts.googleapis.com/css2?family=Oswald:wght@400;500;600;700&family=Roboto:wght@400;500;700&family=Kaushan+Script&display=swap">
<style>
:root{
  --red:#e31b23;
  --red-dark:#b5121a;
  --ink:#141414;
  --night:#0d0d0d;
  --text:#333;
  --muted:#777;
  --line:#dcdcdc;
  --panel:#ececec;
  --blush:#f8e9e9;
  --white:#fff;
}
*{box-sizing:border-box;margin:0;padding:0}
html,body{width:1200px;height:5120px;overflow:hidden}
body{font-family:"Roboto",Arial,sans-serif;color:var(--text);background:var(--white);font-size:16px}
.section{position:relative;width:1200px;overflow:hidden}
.heading{font-family:"Oswald",Arial,sans-serif;font-weight:500;font-size:52px;text-align:center;color:var(--ink);letter-spacing:.5px}
.heading .accent{color:var(--red)}
.heading-rule{width:70px;height:4px;background:var(--red);margin:10px auto 0}
.btn{display:inline-block;background:var(--red);color:var(--white);font-family:"Roboto",sans-serif;font-weight:700;font-size:15px;text-transform:uppercase;padding:14px 28px;border-radius:3px;letter-spacing:.5px;white-space:nowrap}

/* Hero */
.hero{height:660px}
.hero-photo{position:absolute;inset:0;background:radial-gradient(ellipse at 30% 70%,#8a3a1e 0%,#4a1c10 40%,#1c0c08 100%)}
.hero-shade{position:absolute;inset:0;background:linear-gradient(180deg,rgba(0,0,0,.55) 0%,rgba(0,0,0,.15) 40%,rgba(0,0,0,.45) 100%)}
.topbar{position:absolute;top:0;left:360px;right:0;height:34px;background:var(--red);color:var(--white);font-size:12px;display:flex;align-items:center;justify-content:space-between;padding:0 24px;white-space:nowrap}
.topbar span{display:flex;align-items:center;gap:8px}
.brand{position:absolute;top:22px;left:40px;font-family:"Oswald",sans-serif;font-weight:700;font-size:38px;color:var(--white);display:flex;align-items:center;gap:12px;white-space:nowrap}
.brand .dot{width:16px;height:16px;background:var(--red);border-radius:50%}
.nav{position:absolute;top:48px;left:380px;display:flex;gap:4px;align-items:center}
.nav a{color:var(--white);text-decoration:none;font-size:16px;font-weight:500;padding:10px 16px;white-space:nowrap}
.nav a.active{background:var(--red);border-radius:2px}
.nav-icons{position:absolute;top:58px;right:60px;display:flex;gap:22px}
.hero-copy{position:absolute;top:310px;left:0;right:0;text-align:center;color:var(--white)}
.hero-title{font-family:"Oswald",sans-serif;font-weight:600;font-size:74px;line-height:1.05}
.hero-sub{font-size:26px;margin:18px 0 30px}
.dots{position:absolute;bottom:40px;left:0;right:0;display:flex;justify-content:center;gap:10px}
.dots i{width:10px;height:10px;border-radius:50%;background:rgba(255,255,255,.5)}
.dots i.on{background:var(--white)}

/* Specials */
.specials{height:560px;padding-top:100px}
.special-grid{display:flex;gap:28px;justify-content:center;margin-top:50px}
.special-card{position:relative;width:468px;height:290px;background:var(--ink);border-radius:8px;overflow:hidden;color:var(--white)}
.special-photo{position:absolute;right:0;top:0;width:270px;height:100%;background:radial-gradient(circle at 50% 55%,#c98b3e 0%,#6a3a1a 45%,#1a1a1a 80%)}
.special-photo.spicy{background:radial-gradient(circle at 50% 55%,#b4502a 0%,#5a2414 45%,#1a1a1a 80%)}
.special-text{position:absolute;left:30px;top:56px}
.special-script{font-family:"Kaushan Script",cursive;font-size:34px}
.special-name{font-family:"Oswald",sans-serif;font-size:34px;font-weight:600;letter-spacing:1px}
.special-note{font-size:18px;font-weight:700;margin:4px 0 24px}
.badge{position:absolute;top:16px;right:16px;width:60px;height:60px;border-radius:50%;background:var(--white);color:var(--ink);font-size:12px;font-weight:700;text-align:center;padding-top:14px;line-height:1.2}

/* About */
.about{height:540px;background:var(--night)}
.about-photo{position:absolute;left:0;top:0;width:610px;height:540px;background:linear-gradient(160deg,#2a2a2a 0%,#6b6a2a 45%,#d8c640 60%,#3a3a3a 100%)}
.about-panel{position:absolute;left:620px;top:30px;width:470px;height:480px;background:var(--red-dark);color:var(--white);padding:40px 36px}
.about-panel h2{font-family:"Oswald",sans-serif;font-weight:500;font-size:46px}
.about-panel .rule{width:60px;height:3px;background:var(--white);margin:8px 0 22px}
.about-panel p{font-size:13px;line-height:1.6;margin-bottom:12px}
.btn-light{background:var(--white);color:var(--red)}

/* Menu */
.menu{height:800px;padding-top:60px}
.menu-sub{text-align:center;color:var(--muted);font-size:17px;margin-top:16px}
.tabs{display:flex;justify-content:center;gap:48px;margin-top:30px;border-bottom:1px solid var(--line);width:976px;margin-left:112px;padding-bottom:14px}
.tabs span{font-size:15px;color:var(--muted);white-space:nowrap}
.tabs span.on{color:var(--red);font-weight:700;position:relative}
.tabs span.on::after{content:"";position:absolute;left:0;right:0;bottom:-16px;height:3px;background:var(--red)}
.menu-grid{display:grid;grid-template-columns:440px 440px;column-gap:96px;row-gap:34px;margin:44px 0 0 112px}
.dish{display:flex;align-items:center;gap:18px}
.dish-photo{width:70px;height:70px;border-radius:50%;background:radial-gradient(circle,#9a6a3a,#3a2414);flex:none}
.dish-body{flex:1}
.dish-top{display:flex;align-items:baseline;gap:8px}
.dish-name{font-family:"Oswald",sans-serif;font-size:22px;font-weight:500;color:var(--ink);white-space:nowrap}
.dish-leader{flex:1;border-bottom:1px dotted #aaa}
.dish-price{font-size:20px;color:var(--ink)}
.dish-desc{font-size:13px;color:var(--muted);margin-top:4px}
.menu-cta{text-align:center;margin-top:52px}

/* Retail */
.retail{height:560px;background:linear-gradient(180deg,#1a1a1a,#0a0a0a)}
.retail-title{position:absolute;left:112px;top:64px;font-family:"Oswald",sans-serif;font-size:46px;font-weight:500;color:var(--white)}
.retail-title .accent{color:var(--red)}
.retail-arrows{position:absolute;right:112px;top:76px;display:flex;gap:8px}
.retail-arrows i{width:26px;height:26px;border-radius:50%;background:var(--red);display:flex;align-items:center;justify-content:center}
.retail-arrows i.dim{background:#555}
.product{position:absolute;top:168px;width:310px;height:352px;border-radius:4px;overflow:hidden}
.product-photo{position:absolute;inset:0}
.product-label{position:absolute;bottom:44px;left:0;right:0;text-align:center;color:var(--white);font-family:"Oswald",sans-serif;font-size:28px;letter-spacing:1px}
.product-btn{position:absolute;bottom:10px;left:50%;transform:translateX(-50%);width:26px;height:22px;background:var(--red);border-radius:3px}

/* FAQ */
.faq{height:600px;padding-top:80px}
.faq-list{position:absolute;left:112px;top:230px;width:500px}
.faq-item{height:52px;border:1px solid var(--line);margin-bottom:12px;display:flex;align-items:center;justify-content:space-between;padding:0 18px;font-size:14px;color:var(--muted);background:var(--white)}
.faq-item.on{background:var(--red);color:var(--white);font-weight:700;border-color:var(--red)}
.faq-answer{position:absolute;left:640px;top:230px;width:448px;height:300px;background:var(--panel);padding:34px}
.faq-answer h3{font-size:18px;color:var(--ink);margin-bottom:14px;font-weight:500}
.faq-answer p{font-size:14px;line-height:1.6;color:var(--muted)}

/* Info */
.info{height:480px;background:linear-gradient(180deg,#181818,#2b2b2b)}
.info .heading{color:var(--white);padding-top:50px}
.info-grid{position:absolute;top:160px;left:112px;display:flex;gap:24px}
.info-card{width:226px;height:200px;background:var(--white);border-radius:8px;padding:26px 22px}
.info-head{display:flex;align-items:center;gap:14px;margin-bottom:16px}
.info-icon{width:44px;height:44px;border-radius:50%;background:var(--red);display:flex;align-items:center;justify-content:center;flex:none}
.info-head h3{font-family:"Oswald",sans-serif;font-weight:500;font-size:22px;color:var(--ink)}
.info-card p{font-size:13px;line-height:1.6;color:var(--muted)}

/* Contact */
.contact{height:540px}
.map{position:absolute;left:112px;top:60px;width:580px;height:420px;background:linear-gradient(135deg,#e6e3dc,#d2dbe3 60%,#e8e2d6)}
.contact-panel{position:absolute;left:692px;top:60px;width:396px;height:420px;background:var(--blush);padding:30px 32px}
.contact-row{display:flex;gap:16px;margin-bottom:26px}
.contact-icon{width:36px;height:36px;background:var(--red);border-radius:4px;display:flex;align-items:center;justify-content:center;flex:none}
.contact-row h4{font-family:"Oswald",sans-serif;font-weight:500;font-size:22px;color:var(--red)}
.contact-row p{font-size:14px;color:var(--text);margin-top:4px;line-height:1.5}

/* Footer */
.footer{height:380px;background:var(--night);color:#bbb}
.footer-brand{position:absolute;left:112px;top:60px;font-family:"Oswald",sans-serif;font-weight:700;font-size:36px;color:var(--white)}
.footer-about{position:absolute;left:112px;top:130px;width:290px;font-size:13px;line-height:1.6}
.socials{position:absolute;left:112px;top:250px;display:flex;gap:10px}
.socials i{width:30px;height:30px;border-radius:50%;background:var(--white)}
.footer-col{position:absolute;top:72px}
.footer-col h4{font-family:"Oswald",sans-serif;color:var(--white);font-weight:500;font-size:20px;margin-bottom:20px;white-space:nowrap}
.footer-col li{list-style:none;font-size:14px;margin-bottom:10px}
.footer-col li::before{content:"›";color:var(--red);margin-right:8px}
.news-input{width:260px;height:40px;background:#222;border:1px solid #333;font-size:13px;color:#888;padding:12px}
.news-btn{margin-top:12px;padding:12px 22px}
.footer-bottom{position:absolute;left:0;right:0;bottom:0;height:44px;border-top:1px solid #222;text-align:center;font-size:13px;line-height:44px}
</style>
</head>
<body>

<header class="section hero">
  <div class="hero-photo" role="img" aria-label="Close-up of a sizzling breakfast plate with glazed ham"></div>
  <div class="hero-shade"></div>
  <div class="topbar">
    <span><svg width="12" height="14" viewBox="0 0 12 14"><path d="M6 0a5 5 0 0 0-5 5c0 4 5 9 5 9s5-5 5-9a5 5 0 0 0-5-5z" fill="#fff"/><circle cx="6" cy="5" r="2" fill="#e31b23"/></svg>1840 Harlow Avenue Brookvale, Michigan 48000</span>
    <span>(555) 014-2288</span>
    <span>hello@thecopperkitebrookvale.com</span>
    <span>Sat - 8 a.m. - 3 p.m.</span>
  </div>
  <div class="brand"><span class="dot"></span>The Copper Kite</div>
  <nav class="nav">
    <a class="active">Home</a><a>About Us</a><a>Menu</a><a>Retail</a><a>Press</a><a>Contact Us</a>
  </nav>
  <div class="nav-icons">
    <svg width="20" height="18" viewBox="0 0 20 18"><path d="M1 1h3l2 10h11l2-7H5" fill="none" stroke="#fff" stroke-width="2"/><circle cx="8" cy="15" r="1.6" fill="#fff"/><circle cx="15" cy="15" r="1.6" fill="#fff"/></svg>
    <svg width="18" height="18" viewBox="0 0 18 18"><circle cx="9" cy="6" r="4" fill="none" stroke="#fff" stroke-width="2"/><path d="M2 17c1-4 4-5 7-5s6 1 7 5" fill="none" stroke="#fff" stroke-width="2"/></svg>
    <svg width="18" height="18" viewBox="0 0 18 18"><circle cx="7.5" cy="7.5" r="5.5" fill="none" stroke="#fff" stroke-width="2"/><path d="M12 12l5 5" stroke="#fff" stroke-width="2"/></svg>
  </div>
  <div class="hero-copy">
    <h1 class="hero-title">Authentic flavors, from<br>our kitchen to you</h1>
    <p class="hero-sub">Authentic dishes inspired by timeless traditions.</p>
    <span class="btn">Get Started</span>
  </div>
  <div class="dots"><i class="on"></i><i></i><i></i></div>
</header>

<section class="section specials">
  <h2 class="heading">Our <span class="accent">Daily Specials</span></h2>
  <div class="heading-rule"></div>
  <div class="special-grid">
    <article class="special-card">
      <div class="special-photo" role="img" aria-label="Plate of huevos with fried egg and toast"></div>
      <div class="badge">Only<br>$8</div>
      <div class="special-text">
        <div class="special-script">Delicious</div>
        <div class="special-name">HUEVOS</div>
        <div class="special-note">Limited Offer</div>
        <span class="btn">Order Now</span>
      </div>
    </article>
    <article class="special-card">
      <div class="special-photo spicy" role="img" aria-label="Bowl of spicy rumble hash"></div>
      <div class="badge">Only<br>$10</div>
      <div class="special-text">
        <div class="special-script">Spicy</div>
        <div class="special-name">RUMBLE</div>
        <div class="special-note">Limited Offer</div>
        <span class="btn">Order Now</span>
      </div>
    </article>
  </div>
</section>

<section class="section about">
  <div class="about-photo" role="img" aria-label="Storefront of the restaurant with a yellow entrance"></div>
  <div class="about-panel">
    <h2>About Us</h2>
    <div class="rule"></div>
    <p>The doors of The Copper Kite first swung open on a quiet December morning. We welcomed our first guests and started our neighborhood life as a business that still carries on today. Along with good food and happier guests, we found many friends along the way.</p>
    <p>The most frequent question we hear is simple: why the name? We always answer that it came from a long story told across the counter, and that the real answer is best shared over a warm plate and a fresh cup of coffee.</p>
    <span class="btn btn-light">Read More</span>
  </div>
</section>

<section class="section menu">
  <h2 class="heading">Our Restaurant <span class="accent">Foods Menu</span></h2>
  <p class="menu-sub">Savor artistry, innovation, and elegance on every plate.</p>
  <div class="tabs">
    <span class="on">All Things Eggs</span><span>Sugar Shakes</span><span>Green things</span><span>Breads</span><span>Other Stuffs</span><span>Whistle Wetters</span><span>B. Sides</span>
  </div>
  <div class="menu-grid">
    <div class="dish"><div class="dish-photo" role="img" aria-label="Green eggs and ham"></div><div class="dish-body"><div class="dish-top"><span class="dish-name">Green Eggs and Ham</span><span class="dish-leader"></span><span class="dish-price">$13.95</span></div><div class="dish-desc">Pesto Scramble</div></div></div>
    <div class="dish"><div class="dish-photo" role="img" aria-label="Cowboy skillet"></div><div class="dish-body"><div class="dish-top"><span class="dish-name">Cowboy Cole</span><span class="dish-leader"></span><span class="dish-price">$17.95</span></div><div class="dish-desc">Pork Hash</div></div></div>
    <div class="dish"><div class="dish-photo" role="img" aria-label="Two plain eggs"></div><div class="dish-body"><div class="dish-top"><span class="dish-name">Eggs ala Boring</span><span class="dish-leader"></span><span class="dish-price">$7.95</span></div><div class="dish-desc">Simple Two Eggs</div></div></div>
    <div class="dish"><div class="dish-photo" role="img" aria-label="Bocca al Lupo plate"></div><div class="dish-body"><div class="dish-top"><span class="dish-name">Bocca al Lupo</span><span class="dish-leader"></span><span class="dish-price">$12.95</span></div><div class="dish-desc">Hot Italian Sausage</div></div></div>
    <div class="dish"><div class="dish-photo" role="img" aria-label="Red flannel hash"></div><div class="dish-body"><div class="dish-top"><span class="dish-name">Red Flannel Hash</span><span class="dish-leader"></span><span class="dish-price">$13.95</span></div><div class="dish-desc">Red Spiced Beef Brisket</div></div></div>
    <div class="dish"><div class="dish-photo" role="img" aria-label="The Forager plate"></div><div class="dish-body"><div class="dish-top"><span class="dish-name">The Forager</span><span class="dish-leader"></span><span class="dish-price">$17.95</span></div><div class="dish-desc">Morels, Garlic Sour Cream</div></div></div>
    <div class="dish"><div class="dish-photo" role="img" aria-label="Crab cakes and eggs"></div><div class="dish-body"><div class="dish-top"><span class="dish-name">Crab Cakes and Eggs</span><span class="dish-leader"></span><span class="dish-price">$16.95</span></div><div class="dish-desc">Two Crab Cakes</div></div></div>
    <div class="dish"><div class="dish-photo" role="img" aria-label="Huevos rancheros"></div><div class="dish-body"><div class="dish-top"><span class="dish-name">Huevos Rancheros</span><span class="dish-leader"></span><span class="dish-price">$12.95</span></div><div class="dish-desc">Two Eggs Any Style</div></div></div>
  </div>
  <div class="menu-cta"><span class="btn">View All</span></div>
</section>

<section class="section retail">
  <h2 class="retail-title"><span class="accent">OUR</span> RETAIL</h2>
  <div class="retail-arrows">
    <i class="dim"><svg width="10" height="10" viewBox="0 0 10 10"><path d="M7 1L3 5l4 4" fill="none" stroke="#fff" stroke-width="2"/></svg></i>
    <i><svg width="10" height="10" viewBox="0 0 10 10"><path d="M3 1l4 4-4 4" fill="none" stroke="#fff" stroke-width="2"/></svg></i>
  </div>
  <div class="product" style="left:112px">
    <div class="product-photo" role="img" aria-label="Bottles of house hot sauce" style="background:linear-gradient(180deg,#3a4a8a,#c0392b 55%,#1a1a1a)"></div>
    <div class="product-label">SAUCE</div><div class="product-btn"></div>
  </div>
  <div class="product" style="left:445px">
    <div class="product-photo" role="img" aria-label="Plain white house t-shirt" style="background:linear-gradient(180deg,#2a2a2a,#e8e8e8 50%,#2a2a2a)"></div>
    <div class="product-label">SAUCE</div><div class="product-btn"></div>
  </div>
  <div class="product" style="left:778px">
    <div class="product-photo" role="img" aria-label="Red gift card with ribbon" style="background:linear-gradient(160deg,#2a0a0a,#c2161d 50%,#3a0a0a)"></div>
    <div class="product-label">SAUCE</div><div class="product-btn"></div>
  </div>
</section>

<section class="section faq">
  <h2 class="heading">FREQUENTLY <span class="accent">ASKED QUESTIONS</span></h2>
  <div class="heading-rule"></div>
  <div class="faq-list">
    <div class="faq-item">1.Do you take reservations?<svg width="12" height="8" viewBox="0 0 12 8"><path d="M1 1l5 5 5-5" fill="none" stroke="#999" stroke-width="2"/></svg></div>
    <div class="faq-item">2.Do you do carry out?<svg width="12" height="8" viewBox="0 0 12 8"><path d="M1 1l5 5 5-5" fill="none" stroke="#999" stroke-width="2"/></svg></div>
    <div class="faq-item">3.Do you deliver?<svg width="12" height="8" viewBox="0 0 12 8"><path d="M1 1l5 5 5-5" fill="none" stroke="#999" stroke-width="2"/></svg></div>
    <div class="faq-item">4.How large is your restaurant?<svg width="12" height="8" viewBox="0 0 12 8"><path d="M1 1l5 5 5-5" fill="none" stroke="#999" stroke-width="2"/></svg></div>
    <div class="faq-item on">5.Why didn't you answer my question?<svg width="12" height="8" viewBox="0 0 12 8"><path d="M1 7l5-5 5 5" fill="none" stroke="#fff" stroke-width="2"/></svg></div>
  </div>
  <div class="faq-answer">
    <h3>5.Why didn't you answer my question?</h3>
    <p>We didn't know you had one! Please email us with any questions not covered within the pages of this website.</p>
  </div>
</section>

<section class="section info">
  <h2 class="heading">General <span class="accent">Informations</span></h2>
  <div class="info-grid">
    <div class="info-card">
      <div class="info-head"><span class="info-icon"><svg width="22" height="22" viewBox="0 0 22 22"><circle cx="11" cy="11" r="9" fill="none" stroke="#fff" stroke-width="2"/><path d="M11 6v5l4 2" fill="none" stroke="#fff" stroke-width="2"/></svg></span><h3>Hours</h3></div>
      <p>Saturday through Sunday, 8 a.m. until 3 p.m. Please call for any holiday hours information.</p>
    </div>
    <div class="info-card">
      <div class="info-head"><span class="info-icon"><svg width="22" height="22" viewBox="0 0 22 22"><path d="M4 7h12v6a5 5 0 0 1-5 5h-2a5 5 0 0 1-5-5z" fill="none" stroke="#fff" stroke-width="2"/><path d="M16 9h2a2 2 0 0 1 0 4h-2" fill="none" stroke="#fff" stroke-width="2"/></svg></span><h3>Brunch</h3></div>
      <p>Brunch is what we call our menu, and ALL items are available ALL hours we are open!</p>
    </div>
    <div class="info-card">
      <div class="info-head"><span class="info-icon"><svg width="22" height="22" viewBox="0 0 22 22"><path d="M5 3h12l-6 8z" fill="none" stroke="#fff" stroke-width="2"/><path d="M11 11v8M7 19h8" stroke="#fff" stroke-width="2"/></svg></span><h3>Booze</h3></div>
      <p>We have a full bar! Beer, wine and mimosas. Catch a Buzz at The Kite!</p>
    </div>
    <div class="info-card">
      <div class="info-head"><span class="info-icon"><svg width="22" height="22" viewBox="0 0 22 22"><rect x="2" y="5" width="18" height="12" rx="2" fill="none" stroke="#fff" stroke-width="2"/><path d="M2 9h18" stroke="#fff" stroke-width="2"/></svg></span><h3>Plastic</h3></div>
      <p>We gladly accept all major credit cards!</p>
    </div>
  </div>
</section>

<section class="section contact">
  <div class="map" role="img" aria-label="Street map of the neighborhood around the restaurant"></div>
  <div class="contact-panel">
    <div class="contact-row"><span class="contact-icon"><svg width="18" height="18" viewBox="0 0 22 22"><circle cx="11" cy="11" r="9" fill="none" stroke="#fff" stroke-width="2"/><path d="M11 6v5l4 2" fill="none" stroke="#fff" stroke-width="2"/></svg></span><div><h4>Opening Hours</h4><p>Sat. - Sun. 8 a.m. - 3 p.m.</p></div></div>
    <div class="contact-row"><span class="contact-icon"><svg width="14" height="18" viewBox="0 0 12 14"><path d="M6 0a5 5 0 0 0-5 5c0 4 5 9 5 9s5-5 5-9a5 5 0 0 0-5-5z" fill="#fff"/><circle cx="6" cy="5" r="2" fill="#e31b23"/></svg></span><div><h4>Visit Us</h4><p>1840 Harlow Avenue Brookvale, Michigan 48000</p></div></div>
    <div class="contact-row"><span class="contact-icon"><svg width="18" height="18" viewBox="0 0 20 20"><path d="M4 2h4l2 5-3 2a11 11 0 0 0 4 4l2-3 5 2v4a2 2 0 0 1-2 2A16 16 0 0 1 2 4a2 2 0 0 1 2-2z" fill="#fff"/></svg></span><div><h4>Call Us</h4><p>(555) 014-2288</p></div></div>
    <div class="contact-row"><span class="contact-icon"><svg width="18" height="14" viewBox="0 0 20 14"><rect x="1" y="1" width="18" height="12" fill="none" stroke="#fff" stroke-width="2"/><path d="M1 1l9 7 9-7" fill="none" stroke="#fff" stroke-width="2"/></svg></span><div><h4>Mail Us</h4><p>hello@thecopperkitebrookvale.com</p></div></div>
  </div>
</section>

<footer class="section footer">
  <div class="footer-brand">The Copper Kite</div>
  <p class="footer-about">We took a small neighborhood corner and decided to transform it into a place where friends gather, where good food is made by hand, and where every guest is welcome at our counter.</p>
  <div class="socials"><i></i><i></i><i></i><i></i><i></i></div>
  <div class="footer-col" style="left:480px"><h4>Quick Links</h4><ul><li>Home</li><li>About Us</li><li>Menu</li><li>Retail</li><li>Press</li><li>Contact Us</li></ul></div>
  <div class="footer-col" style="left:660px"><h4>Quick Links</h4><ul><li>Privacy Policy</li><li>Terms &amp; Conditions</li><li>Disclaimer</li><li>Support</li></ul></div>
  <div class="footer-col" style="left:840px"><h4>Subscribe To Our Newsletter</h4><div class="news-input">Enter Email Address</div><span class="btn news-btn">Subscribe</span></div>
  <div class="footer-bottom">Copyright © 2024 - The Copper Kite. All rights reserved.</div>
</footer>

</body>
</html>
```